Vorn upkeep KT Solar Venture

Solar power system install
Services and maintenance
wiring, Rewinding and Renovation
Switch Board Upgrade
Power and lighting point
t doesn’t matter how much you spend on quality parts, your solar system will let you down if your design and installation are sub-par. Have your solar system tailored and installed by our Master Electrician and Bright Grid Guild Accredited team.

Target Market(s)

sales and installed

Industry/Entity Type

Solar install and retailer

Contact Information for Business Card

Name , Email, Phone Number ,Business address,

Font styles to use
Serif

Colors
0054AA
0677BA
7BADD7
CADEEF
E8F1F8

Requirements
Must have
• clear and bright
Nice to have
• new design
Should not have
• unclear pictures

```html
<!DOCTYPE html>
<html lang="en">
<head>
<meta charset="utf-8">
<title>Vorn upkeep – Business Card</title>
<link rel="stylesheet" href="https://fonts.googleapis.com/css2?family=Roboto:wght@400;500&display=swap">
<style>
  :root {
    --backdrop: #e7e4e0;
    --card: #f6f8fa;
    --card-edge: #dde3e8;
    --blue: #0054aa;
    --ink: #1c1c1c;
    --icon: #1f8a3d;
    --mark-fill: #cadeef;
  }
  * { margin: 0; padding: 0; box-sizing: border-box; }
  html, body {
    width: 1200px;
    height: 1054px;
    overflow: hidden;
    background: var(--backdrop);
  }
  .business-card {
    position: absolute;
    left: 120px;
    top: 237px;
    width: 960px;
    height: 580px;
    background: var(--card);
    border: 1px solid var(--card-edge);
    border-radius: 20px;
    box-shadow: 0 10px 30px rgba(0,0,0,0.12);
  }
  .company {
    position: absolute;
    left: 51px;
    top: 70px;
    font-family: "Roboto", Arial, sans-serif;
    font-weight: 500;
    font-size: 44px;
    line-height: 1;
    color: var(--blue);
  }
  .person {
    position: absolute;
    left: 51px;
    top: 222px;
    font-family: "Roboto", Arial, sans-serif;
  }
  .person-name {
    font-size: 37px;
    font-weight: 500;
    color: var(--blue);
  }
  .person-role {
    margin-top: 8px;
    font-size: 24px;
    color: var(--ink);
  }
  .address {
    position: absolute;
    left: 51px;
    top: 340px;
    font-family: "Roboto", Arial, sans-serif;
    font-size: 24px;
    line-height: 37px;
    color: var(--ink);
    font-style: normal;
  }
  .contact-list {
    position: absolute;
    left: 51px;
    top: 420px;
    list-style: none;
    font-family: "Roboto", Arial, sans-serif;
    font-size: 24px;
    color: var(--ink);
  }
  .contact-list li {
    display: flex;
    align-items: center;
    height: 37px;
  }
  .contact-icon {
    width: 22px;
    height: 22px;
    margin-right: 27px;
    fill: var(--icon);
  }
  .brand-mark {
    position: absolute;
    left: 470px;
    top: 60px;
    width: 420px;
    height: 460px;
    display: flex;
    flex-direction: column;
    align-items: center;
    justify-content: center;
  }
  .brand-dot {
    width: 300px;
    height: 300px;
    border-radius: 50%;
    background: var(--mark-fill);
  }
  .brand-name {
    margin-top: 26px;
    font-family: "Roboto", Arial, sans-serif;
    font-weight: 500;
    font-size: 40px;
    color: var(--blue);
    line-height: 1;
  }
</style>
</head>
<body>
  <article class="business-card">
    <h1 class="company">Vorn upkeep</h1>

    <div class="person">
      <p class="person-name">Dana Ellis Hart</p>
      <p class="person-role">Managing Director</p>
    </div>

    <address class="address">
      58 Larkmere Rd., Tallow Bay,<br>
      Fenwick, US 204817
    </address>

    <ul class="contact-list">
      <li>
        <svg class="contact-icon" viewBox="0 0 24 24" aria-hidden="true">
          <path d="M3 9c0-3 4-5 9-5s9 2 9 5v2h-5V8.5c-1.3-.4-2.6-.6-4-.6s-2.7.2-4 .6V11H3z"/>
          <path d="M6 12h12l2 8H4z"/>
        </svg>
        <span>555-014-2290</span>
      </li>
      <li>
        <svg class="contact-icon" viewBox="0 0 24 24" aria-hidden="true">
          <path d="M2 5h20v14H2z M4 7v.5l8 6 8-6V7z" fill-rule="evenodd"/>
        </svg>
        <span>dana@vornupkeep.com</span>
      </li>
      <li>
        <svg class="contact-icon" viewBox="0 0 24 24" aria-hidden="true">
          <circle cx="12" cy="12" r="10"/>
          <path d="M2 12h20M12 2c3 3 3 17 0 20M12 2c-3 3-3 17 0 20M4 7h16M4 17h16" stroke="#f6f8fa" stroke-width="1.4" fill="none"/>
        </svg>
        <span>www.vornupkeep.com</span>
      </li>
    </ul>

    <div class="brand-mark">
      <div class="brand-dot" aria-hidden="true"></div>
      <p class="brand-name">Vorn upkeep</p>
    </div>
  </article>
</body>
</html>
```